German Headhunter/ HR Consultancy needs Business Cards Design

We need a business Card Design for our Company in Stuttgart. We are specialized as Headhunter/ HR Consultancy in Placement of specialist and managers in permanent employment. Please refer to our business logo.

```html
<!DOCTYPE html>
<html lang="de">
<head>
<meta charset="utf-8">
<title>Kernwerk Personalberatung – Visitenkarte</title>
<link href="https://fonts.googleapis.com/css2?family=Montserrat:wght@500;700&family=Arimo:wght@400&display=swap" rel="stylesheet">
<style>
  :root{
    --backdrop:#2b2b2d;
    --card-grey:#97989b;
    --brand-blue:#3a56ab;
    --white:#ffffff;
  }
  *{margin:0;padding:0;box-sizing:border-box}
  html,body{width:1200px;height:1015px;overflow:hidden;background:var(--backdrop)}
  .canvas{position:relative;width:1200px;height:1015px}
  .card{
    position:absolute;left:320px;width:560px;height:320px;
    background:var(--card-grey);overflow:hidden;
    box-shadow:0 10px 24px rgba(0,0,0,.5);
  }
  .card--front{top:110px}
  .card--back{top:575px}

  /* front */
  .lockup{position:absolute;left:50%;top:50%;transform:translate(-50%,-50%);
    display:flex;align-items:center;gap:16px}
  .lockup__square{width:46px;height:46px;background:var(--brand-blue)}
  .lockup__name{font:700 38px/1 'Montserrat',sans-serif;color:var(--brand-blue);letter-spacing:1px}
  .lockup__tagline{font:500 14px/1 'Montserrat',sans-serif;color:var(--white);letter-spacing:1.5px;margin-top:6px}

  /* back */
  .band{position:absolute;inset:0;width:560px;height:320px}
  .brand-mark{position:absolute;right:30px;top:30px;display:flex;align-items:center;gap:10px;z-index:1}
  .brand-mark__square{width:28px;height:28px;background:var(--brand-blue)}
  .brand-mark__name{font:700 24px/1 'Montserrat',sans-serif;color:var(--brand-blue);letter-spacing:1px}
  .contact{position:absolute;left:46px;top:118px;color:var(--white);font-family:'Arimo',sans-serif;z-index:1}
  .contact__name{font:700 19px/1 'Montserrat',sans-serif;letter-spacing:.5px}
  .contact__role{font-size:12px;letter-spacing:1px;margin-top:4px}
  .contact__list{list-style:none;margin-top:14px;font-size:13.5px;line-height:19px}
  .contact__list li{display:flex;align-items:center;gap:8px}
  .contact__list svg{width:13px;height:13px;flex:none}
  .contact__address{margin-top:10px;margin-left:21px;font-size:13.5px;line-height:18px}
</style>
</head>
<body>
<main class="canvas">
  <section class="card card--front" aria-label="Vorderseite">
    <div class="lockup">
      <span class="lockup__square"></span>
      <div>
        <div class="lockup__name">KERNWERK</div>
        <div class="lockup__tagline">PERSONALBERATUNG</div>
      </div>
    </div>
  </section>

  <section class="card card--back" aria-label="Rückseite">
    <svg class="band" viewBox="0 0 560 320" aria-hidden="true">
      <polygon points="0,100 300,45 430,230 0,300" fill="var(--brand-blue)"/>
    </svg>
    <div class="brand-mark">
      <span class="brand-mark__square"></span>
      <span class="brand-mark__name">KERNWERK</span>
    </div>
    <div class="contact">
      <div class="contact__name">LENA HARTMANN</div>
      <div class="contact__role">MANAGING DIRECTOR</div>
      <ul class="contact__list">
        <li><svg viewBox="0 0 16 16"><path d="M4 1l3 3-2 2c1 2 3 4 5 5l2-2 3 3-2 3C7 15 1 9 1 3z" fill="var(--white)"/></svg>0711-555 0182</li>
        <li><svg viewBox="0 0 16 16"><rect x="1" y="3" width="14" height="10" fill="none" stroke="var(--white)" stroke-width="1.6"/><path d="M1 3l7 6 7-6" fill="none" stroke="var(--white)" stroke-width="1.6"/></svg>kontakt@kernwerk.de</li>
        <li><svg viewBox="0 0 16 16"><circle cx="8" cy="8" r="6.5" fill="none" stroke="var(--white)" stroke-width="1.4"/><ellipse cx="8" cy="8" rx="3" ry="6.5" fill="none" stroke="var(--white)" stroke-width="1.2"/><path d="M1.5 8h13" stroke="var(--white)" stroke-width="1.2"/></svg>www.kernwerk-hr.de</li>
      </ul>
      <div class="contact__address">Rotebühlstraße 58, 2. Etage<br>70178 Stuttgart, Germany</div>
    </div>
  </section>
</main>
</body>
</html>
```